Ward Compass Business Card Design*

We need a business card design for our company Ward Compass. Our company is specialized in providing online consulting services regarding medical institutions, hospitals and doctors. We work with patients worldwide looking to choose between healthcare providers. We have a website you may use as a reference, where we list doctors and clinics worldwide. So we target Medical providers as well as patients worldwide.
Target Market(s)
Medical Providers and patients around the world
Industry/Entity Type
Medical
Contact Information for Business Card
Salwa Kettani
CEO
+90 612 348 2175
info@wardcompass.example
www.wardcompass.example
14 Annakhil 7 H.R.B. Rabat, Morocco
Requirements
Must have
- Company logo/name on one full side, personal info and smaller logo and company name on the other side.
Nice to have
- Smart and elegant design

```html
<!DOCTYPE html>
<html lang="en">
<head>
<meta charset="utf-8">
<title>Ward Compass – Business Card</title>
<link rel="stylesheet" href="https://fonts.googleapis.com/css2?family=Lato:wght@400;700;900&family=Montserrat:wght@600&display=swap">
<style>
  :root {
    --stage: #6a6a6a;
    --card: #fbfbfb;
    --navy: #1f3a6d;
    --ink-grey: #6f6f72;
    --icon: #2e2e30;
  }
  * { box-sizing: border-box; margin: 0; padding: 0; }
  html, body { width: 1200px; height: 1056px; overflow: hidden; }
  body {
    background: var(--stage);
    font-family: "Lato", sans-serif;
    display: flex;
    flex-direction: column;
    align-items: center;
    justify-content: center;
    gap: 56px;
  }
  .card {
    position: relative;
    width: 760px;
    height: 434px;
    background: var(--card);
    box-shadow: 0 10px 24px rgba(0,0,0,.35);
  }
  .brand {
    position: absolute;
    display: flex;
    align-items: center;
    gap: 12px;
    font-family: "Montserrat", sans-serif;
    font-weight: 600;
    color: var(--navy);
    letter-spacing: .04em;
    text-transform: uppercase;
    white-space: nowrap;
  }
  .brand-dot {
    width: 34px; height: 34px;
    border-radius: 50%;
    background: var(--navy);
  }
  .card-front .brand { top: 56px; right: 48px; font-size: 22px; }
  .card-back .brand { left: 60px; bottom: 96px; font-size: 26px; }
  .card-back .brand-dot { width: 40px; height: 40px; }

  .holder { position: absolute; left: 60px; top: 196px; }
  .holder-name {
    font-weight: 900;
    font-size: 30px;
    color: var(--navy);
    letter-spacing: .01em;
    text-transform: uppercase;
  }
  .holder-role { font-size: 16px; color: var(--ink-grey); margin-top: 2px; }
  .contact-list { list-style: none; margin-top: 10px; }
  .contact-list li {
    display: flex; align-items: center; gap: 14px;
    font-size: 16px; line-height: 24px; color: var(--ink-grey);
  }
  .contact-list svg { width: 13px; height: 13px; fill: var(--icon); flex: none; }
</style>
</head>
<body>
  <section class="card card-front" aria-label="Business card, front">
    <div class="brand"><span class="brand-dot"></span>Ward Compass</div>
    <div class="holder">
      <h1 class="holder-name">Salwa Kettani</h1>
      <p class="holder-role">CEO</p>
      <ul class="contact-list">
        <li><svg viewBox="0 0 16 16" aria-hidden="true"><path d="M3.6 1.2l2.3 2.6c.4.4.3 1-.1 1.4L4.6 6.3c.9 2 2.6 3.8 4.8 4.9l1.1-1.2c.4-.4 1-.5 1.4-.1l2.6 2.2c.4.4.4 1 0 1.4l-1.3 1.3C11.6 16.4 7 14.5 4.1 11.4 1.3 8.4-.4 4 1.2 2.4L2.3 1.2c.4-.4 1-.4 1.3 0z"/></svg>+90 612 348 2175</li>
        <li><svg viewBox="0 0 16 16" aria-hidden="true"><path d="M1 3h14v1.2L8 8.8 1 4.2z"/><path d="M1 5.6l7 4.6 7-4.6V13H1z"/></svg>info@wardcompass.example</li>
        <li><svg viewBox="0 0 16 16" aria-hidden="true"><path d="M8 1a7 7 0 100 14A7 7 0 008 1zm4.9 6.2h-2.2a11 11 0 00-.9-4.1 5.5 5.5 0 013.1 4.1zM8 2.6c.6.8 1.2 2.5 1.3 4.6H6.7C6.8 5.1 7.4 3.4 8 2.6zM6.2 3.1a11 11 0 00-.9 4.1H3.1a5.5 5.5 0 013.1-4.1zM3.1 8.8h2.2c.1 1.5.4 2.9.9 4.1a5.5 5.5 0 01-3.1-4.1zM8 13.4c-.6-.8-1.2-2.5-1.3-4.6h2.6c-.1 2.1-.7 3.8-1.3 4.6zm1.8-.5c.5-1.2.8-2.6.9-4.1h2.2a5.5 5.5 0 01-3.1 4.1z"/></svg>www.wardcompass.example</li>
        <li><svg viewBox="0 0 16 16" aria-hidden="true"><path d="M8 0.8a5 5 0 00-5 5c0 3.7 5 9.4 5 9.4s5-5.7 5-9.4a5 5 0 00-5-5zm0 7a2 2 0 110-4 2 2 0 010 4z"/></svg>14 Annakhil 7 H.R.B. Rabat, Morocco</li>
      </ul>
    </div>
  </section>

  <section class="card card-back" aria-label="Business card, back">
    <div class="brand"><span class="brand-dot"></span>Ward Compass</div>
  </section>
</body>
</html>
```